Construction Company

Design a clutter free business card, it can be double-sided utilizing the logo for VKM Ltd simple with all relevant contact information.

Please also a letterhead design to function for the purposes of invoicing, all mail requirements, with header to be distinctive while the footer ties page together and incorporates all necessary information.

For now, please use generic / dummy text and when a winner is selected, I will disclose the contact information.

Hi Designers! Please read the updated brief which includes the design of a business card and letterhead. Thank you!

```html
<!DOCTYPE html>
<html lang="en">
<head>
<meta charset="utf-8">
<title>VKM Ltd – Business Card</title>
<link rel="stylesheet" href="https://fonts.googleapis.com/css2?family=Montserrat:wght@400;500;700&display=swap">
<style>
  :root {
    --brand-blue: #0a2f96;
    --brand-blue-light: #0d39b0;
    --brand-gold: #b8900f;
    --ink: #2b2b2b;
    --paper: #ffffff;
    --stage: #e7e8ec;
  }
  * { margin: 0; padding: 0; box-sizing: border-box; }
  html, body {
    width: 1200px; height: 881px; overflow: hidden;
    background: var(--stage);
    font-family: "Montserrat", Arial, sans-serif;
  }
  .stage {
    width: 1200px; height: 881px;
    display: flex; flex-direction: column;
    align-items: center; justify-content: center; gap: 40px;
  }
  .card {
    position: relative;
    width: 660px; height: 377px;
    border-radius: 18px;
    overflow: hidden;
    box-shadow: 0 6px 18px rgba(0,0,0,.18);
  }
  /* Back side */
  .card-back {
    background: var(--brand-blue);
    display: flex; align-items: center; justify-content: center;
  }
  .card-back .wordmark {
    color: var(--brand-blue-light);
    font-weight: 700;
    font-size: 72px;
    letter-spacing: 2px;
  }
  /* Front side */
  .card-front { background: var(--paper); }
  .card-front .swoosh {
    position: absolute; inset: 0; width: 100%; height: 100%;
  }
  .brand {
    position: absolute; left: 48px; top: 128px;
    display: flex; align-items: center; gap: 12px;
  }
  .brand .dot {
    width: 22px; height: 22px; border-radius: 50%;
    background: var(--brand-gold);
  }
  .brand .wordmark {
    color: var(--brand-blue);
    font-weight: 700;
    font-size: 50px;
    letter-spacing: 1px;
  }
  .divider {
    position: absolute; left: 338px; top: 70px;
    width: 2px; height: 150px;
    background: var(--brand-blue);
  }
  .contact {
    position: absolute; left: 362px; top: 66px;
    color: var(--ink);
    font-size: 13px; line-height: 1.45;
  }
  .contact .name {
    color: var(--brand-blue);
    font-weight: 700; font-size: 19px;
    letter-spacing: .5px; text-transform: uppercase;
  }
  .contact .role { font-size: 13px; margin-bottom: 10px; }
  .contact .address { margin-bottom: 10px; }
  .contact .line { display: flex; align-items: center; gap: 8px; }
  .contact .line svg { width: 11px; height: 11px; flex: none; }
</style>
</head>
<body>
<main class="stage">

  <section class="card card-back" aria-label="Card back">
    <span class="wordmark">VKM Ltd</span>
  </section>

  <section class="card card-front" aria-label="Card front">
    <svg class="swoosh" viewBox="0 0 660 377" preserveAspectRatio="none" aria-hidden="true">
      <path d="M290 377 C400 330 520 262 660 232 L660 377 Z" fill="var(--brand-blue)"/>
      <path d="M250 377 C380 315 500 250 620 232 C500 258 390 320 275 377 Z" fill="var(--brand-gold)"/>
    </svg>

    <div class="brand">
      <span class="dot"></span>
      <span class="wordmark">VKM Ltd</span>
    </div>

    <div class="divider"></div>

    <div class="contact">
      <div class="name">Daniel Harper</div>
      <div class="role">Founder</div>
      <div class="address">2715 Linden Avenue<br>Millbrook, DE 19120</div>
      <div class="line">
        <svg viewBox="0 0 12 12"><path d="M2.5 1 L4.5 1 L5.2 3.5 L4 4.6 C4.6 6 5.9 7.3 7.4 8 L8.5 6.8 L11 7.5 L11 9.5 C11 10.3 10.3 11 9.5 11 C5 11 1 7 1 2.5 C1 1.7 1.7 1 2.5 1 Z" fill="var(--brand-blue)"/></svg>
        <span>(302) 555-0148</span>
      </div>
      <div class="line">
        <svg viewBox="0 0 12 12"><rect x="1" y="2.5" width="10" height="7" fill="none" stroke="var(--brand-blue)" stroke-width="1.2"/><path d="M1 2.5 L6 6.5 L11 2.5" fill="none" stroke="var(--brand-blue)" stroke-width="1.2"/></svg>
        <span>info@VKMLtd.com</span>
      </div>
      <div class="line">
        <svg viewBox="0 0 12 12"><circle cx="6" cy="6" r="5" fill="none" stroke="var(--brand-blue)" stroke-width="1.1"/><ellipse cx="6" cy="6" rx="2.2" ry="5" fill="none" stroke="var(--brand-blue)" stroke-width="1"/><path d="M1 6 H11" stroke="var(--brand-blue)" stroke-width="1"/></svg>
        <span>www.VKMLtd.com</span>
      </div>
    </div>
  </section>

</main>
</body>
</html>
```